Business Card - high end, modern health care

Hey designers!

We need a double sided business card for the boutique, cutting edge physical therapy rehabilitation centre in Sydney's Northern Beaches.

With the most qualified physios in the area The Harbourview Motion Clinic does what other physiotherapy practices do not, we take our time with our patients giving them longer appointments, better physios and therefor faster results!

We guarantee that the service people receive at THMC will be unparalleled.

Hence we need a business card to reflect our modern, boutique, high end service. The final design needs to reflect that we are in a class of our own yet with the feel of beachside retreat.

Below I have attached our logo in both blue on white and white on blue. The exact colour is;
and the font that we have used in our logo is Tex Gyre Aventador.

I like the idea of the blue as the main colour as it is more eye catching and our signage onto the main road will be in this blue and in the interest of consistency across marketing the blue needs to be a part of the design. However I would appreciate a few designs onto a wooden background as this is a visual theme within the fitout of the practice.

The design needs to be of standard size (91x55mm).

Target Market(s)

We target people who have an end outcome in mind and those who have had poor experiences with other providers and ensure that everyone gets the care that they deserve with a premium service that is tailored to the individuals circumstances. As a premium service, the target market is highly educated, business and tech savvy with the additional target market of elderly people who have self funded their retirement and see value in paying for the best ongoing rehabilitation to maintain independence.

Industry/Entity Type

Physical Therapy

Contact Information for Business Card

Name, designation( Titled Musculoskeletal Physiotherapist... there will also be those in the company that have multiple designations ie 5 or 6 words long), phone number, email, facebook, instagram, address

Font styles to use
Sans Serif

Colors

Designer to choose colors to be used in the design.

Requirements
Must have
• Front - The logo as large as possible, blue or wooden theme, and all of the important details.
• Back - A blank space/lines on which to write appointment times (no "Appointment, date, time" etc.)
Nice to have
• facebook url
• logos for facebook and instagram
• Mini logos for the phone and email?

```html
<!DOCTYPE html>
<html lang="en">
<head>
<meta charset="UTF-8">
<title>The Harbourview Motion Clinic – Business Card</title>
<link href="https://fonts.googleapis.com/css2?family=Montserrat:wght@500;700&family=Open+Sans:wght@400;600&display=swap" rel="stylesheet">
<style>
  :root {
    --brand-blue: #0a4f9e;
    --brand-blue-dark: #063f82;
    --card-white: #ffffff;
    --card-grey: #e9e9e9;
    --text-grey: #444444;
    --stage: #2a2a2a;
  }
  * { margin: 0; padding: 0; box-sizing: border-box; }
  html, body {
    width: 1200px; height: 900px; overflow: hidden;
    background: var(--stage);
  }
  .stage {
    width: 1200px; height: 900px;
    display: flex; flex-direction: column; align-items: center; justify-content: center;
    gap: 60px;
  }
  .card {
    width: 620px; height: 375px;
    border-radius: 18px;
    overflow: hidden;
    position: relative;
    box-shadow: 0 10px 30px rgba(0,0,0,0.45);
  }

  /* Front */
  .card-front {
    background: linear-gradient(135deg, var(--card-grey) 0%, var(--card-white) 45%, var(--card-white) 100%);
  }
  .card-front .brand {
    position: absolute; left: 34px; top: 144px;
    width: 270px;
    display: flex; align-items: center; gap: 10px;
  }
  .brand-dot {
    width: 46px; height: 46px; border-radius: 50%;
    background: var(--brand-blue); flex-shrink: 0;
  }
  .brand-name {
    font-family: "Montserrat", sans-serif; font-weight: 700;
    color: var(--brand-blue);
    font-size: 18px; line-height: 1.2; letter-spacing: 0.3px;
    text-transform: uppercase; white-space: nowrap;
  }
  .divider {
    position: absolute; left: 330px; top: 70px;
    width: 2px; height: 235px; background: var(--brand-blue);
  }
  .details {
    position: absolute; left: 352px; top: 86px; right: 16px;
    font-family: "Open Sans", sans-serif; color: var(--text-grey);
  }
  .person-name {
    font-family: "Montserrat", sans-serif; font-weight: 700;
    color: var(--brand-blue); font-size: 25px; letter-spacing: 0.5px;
    text-transform: uppercase; white-space: nowrap;
  }
  .person-title { font-size: 14px; margin-top: 2px; }
  .address { font-size: 14px; line-height: 1.45; margin-top: 14px; }
  .contact-list { list-style: none; margin-top: 12px; font-size: 14px; line-height: 1.6; }
  .contact-list li { display: flex; align-items: center; gap: 8px; white-space: nowrap; }
  .contact-list svg { width: 12px; height: 12px; flex-shrink: 0; }
  .web-accent { color: var(--brand-blue); }

  /* Back */
  .card-back { background: var(--card-white); }
  .back-band {
    position: absolute; left: 0; top: 0; right: 0; height: 200px;
    background: linear-gradient(135deg, var(--brand-blue-dark), var(--brand-blue));
    display: flex; align-items: center; justify-content: center; gap: 18px;
  }
  .back-band .brand-dot { background: var(--card-white); width: 64px; height: 64px; }
  .back-band .brand-name { color: var(--card-white); font-size: 28px; }
  .appointment-label {
    position: absolute; right: 46px; top: 226px;
    font-family: "Open Sans", sans-serif; color: var(--brand-blue);
    font-size: 20px;
  }
</style>
</head>
<body>
<main class="stage">
  <section class="card card-front" aria-label="Card front">
    <div class="brand">
      <span class="brand-dot"></span>
      <div class="brand-name">The Harbourview<br>Motion Clinic</div>
    </div>
    <div class="divider"></div>
    <div class="details">
      <div class="person-name">Daniel Reyes</div>
      <div class="person-title">Director</div>
      <div class="address">27 Shoreline Avenue, Unit 4,<br>Harbour Bay, PO 20145</div>
      <ul class="contact-list">
        <li>
          <svg viewBox="0 0 12 12" aria-hidden="true"><path d="M2.5 1h2l1 2.5-1.3 1a6 6 0 0 0 3.3 3.3l1-1.3L11 7.5v2A1.5 1.5 0 0 1 9.5 11 8.5 8.5 0 0 1 1 2.5 1.5 1.5 0 0 1 2.5 1z" fill="#0a4f9e"/></svg>
          +330 5814-2270
        </li>
        <li>
          <svg viewBox="0 0 12 12" aria-hidden="true"><rect x="1" y="2.5" width="10" height="7" rx="1" fill="none" stroke="#0a4f9e" stroke-width="1.2"/><path d="M1.5 3l4.5 3.5L10.5 3" fill="none" stroke="#0a4f9e" stroke-width="1.2"/></svg>
          hello@harbourviewmotion.com
        </li>
        <li>
          <svg viewBox="0 0 12 12" aria-hidden="true"><circle cx="6" cy="6" r="5" fill="none" stroke="#0a4f9e" stroke-width="1.1"/><ellipse cx="6" cy="6" rx="2.2" ry="5" fill="none" stroke="#0a4f9e" stroke-width="1"/><path d="M1 6h10" stroke="#0a4f9e" stroke-width="1"/></svg>
          <span>www.<span class="web-accent">harbourviewmotion</span>.com</span>
        </li>
      </ul>
    </div>
  </section>

  <section class="card card-back" aria-label="Card back">
    <div class="back-band">
      <span class="brand-dot"></span>
      <div class="brand-name">The Harbourview<br>Motion Clinic</div>
    </div>
    <div class="appointment-label">Appointment</div>
  </section>
</main>
</body>
</html>
```